Business Card Design For Marketing Agnecy LVP

Need business card design for marketing agency.

Doug Fenwick
President, CEO
1-555-302-4196
doug@boldpromoperksgroup.example
www.BoldPromoPerksGroup.example

Back Side:
Boost Sales Using Rewards, Incentives & Giveaways
Get A Free Sample Package

Target Market(s)

B2B

Industry/Entity Type

Marketing

Contact Information for Business Card

Doug Fenwick
President, CEO
1-555-302-4196

Back Side:
Get A Free Sample Package

Please note that my current url is OLD DESIGN. I am working on new design and want the business card to match color themes at least on new site. Here is the demo link for new site so you can see the colors I use, etc.

http://layoutcratehub.example/kq/doug/lvp_final/index.html

Requirements
Must have
• Please note that my current url is OLD DESIGN. I am working on new design and want the business card to match color themes at least on new site. Here is the demo link for new site so you can see the colors I use, etc.

Nice to have

Should not have

```html
<!DOCTYPE html>
<html lang="en">
<head>
<meta charset="utf-8">
<title>Bold Promo Perks Group – Business Card</title>
<link href="https://fonts.googleapis.com/css2?family=Roboto:wght@400;500;700&family=Krona+One&display=swap" rel="stylesheet">
<style>
  :root {
    --backdrop: #a9a9a9;
    --card: #f1f1f1;
    --brand-blue: #2b5ea8;
    --brand-dark: #3c3c3e;
    --brand-green: #4caf32;
    --text-dark: #333333;
    --white: #ffffff;
  }
  * { box-sizing: border-box; margin: 0; padding: 0; }
  html, body {
    width: 1200px; height: 576px; overflow: hidden;
    background: var(--backdrop);
    font-family: "Roboto", Arial, sans-serif;
  }
  .card {
    position: absolute; top: 138px;
    width: 484px; height: 293px;
    background: var(--card);
    border-radius: 9px;
    overflow: hidden;
  }
  .card--back { left: 81px; }
  .card--front { left: 602px; }

  .brand {
    position: absolute; left: 0; right: 0;
    display: flex; align-items: center; justify-content: center; gap: 12px;
  }
  .card--back .brand { top: 58px; }
  .card--front .brand { top: 68px; }
  .brand__mark {
    width: 30px; height: 30px; background: var(--brand-blue);
  }
  .brand__name {
    font-family: "Roboto", Arial, sans-serif;
    font-weight: 700; font-size: 31px; color: var(--brand-blue);
    letter-spacing: 0.5px;
  }

  .offer-banner {
    position: absolute; left: 64px; top: 147px; width: 357px; height: 66px;
  }
  .offer-banner svg { position: absolute; inset: 0; }
  .offer-banner__tagline {
    position: absolute; top: 11px; left: 0; right: 0; text-align: center;
    color: var(--white); font-size: 12.5px;
  }
  .offer-banner__cta {
    position: absolute; top: 30px; left: 0; right: 0; text-align: center;
    color: var(--white); font-family: "Krona One", sans-serif; font-size: 11px;
  }
  .back-url {
    position: absolute; top: 240px; left: 0; right: 0; text-align: center;
    font-size: 13px; color: var(--text-dark);
  }
  .back-url span { color: var(--brand-blue); }
  .color-band {
    position: absolute; left: 0; right: 0; bottom: 0; height: 11px; display: flex;
  }
  .color-band__blue { flex: 1; background: var(--brand-blue); }
  .color-band__dark { flex: 1; background: var(--brand-dark); }

  .person {
    position: absolute; right: 290px; top: 160px; text-align: right;
  }
  .person__name { font-size: 20px; font-weight: 500; color: var(--brand-blue); }
  .person__title { font-size: 12.5px; color: var(--text-dark); margin-top: 3px; }
  .contacts {
    position: absolute; left: 217px; top: 154px; list-style: none;
    font-size: 12.5px; color: var(--text-dark);
  }
  .contacts li { display: flex; align-items: center; gap: 9px; height: 18.5px; }
  .contacts svg { width: 12px; height: 12px; fill: var(--brand-blue); }

  .cta-button {
    position: absolute; left: 90px; top: 238px; width: 300px; height: 27px;
  }
  .cta-button svg { position: absolute; inset: 0; }
  .cta-button span {
    position: absolute; inset: 0; display: flex; align-items: center; justify-content: center;
    font-family: "Krona One", sans-serif; font-size: 11px; color: var(--white);
  }
</style>
</head>
<body>

<section class="card card--back">
  <div class="brand">
    <div class="brand__mark"></div>
    <div class="brand__name">Bold Promo Perks Group</div>
  </div>
  <div class="offer-banner">
    <svg viewBox="0 0 357 66" width="357" height="66" aria-hidden="true">
      <polygon points="4,48 180,58 353,48 351,52 180,64 6,52" fill="var(--brand-dark)"/>
      <polygon points="0,4 357,0 350,42 178,52 6,42" fill="var(--brand-green)"/>
    </svg>
    <p class="offer-banner__tagline">Boost Sales Using Rewards, Incentives &amp; Giveaways</p>
    <p class="offer-banner__cta">GET A FREE SAMPLE PACKAGE</p>
  </div>
  <p class="back-url">www.<span>BoldPromoPerksGroup</span>.example</p>
  <div class="color-band">
    <div class="color-band__blue"></div>
    <div class="color-band__dark"></div>
  </div>
</section>

<section class="card card--front">
  <div class="brand">
    <div class="brand__mark"></div>
    <div class="brand__name">Bold Promo Perks Group</div>
  </div>
  <div class="person">
    <p class="person__name">Doug Fenwick</p>
    <p class="person__title">President, CEO</p>
  </div>
  <ul class="contacts">
    <li>
      <svg viewBox="0 0 12 12" aria-hidden="true"><path d="M1 4c0-2 2-3 5-3s5 1 5 3l-2 1-1-2H4L3 5zM3 6h6l1 5H2z"/></svg>
      1-555-302-4196
    </li>
    <li>
      <svg viewBox="0 0 12 12" aria-hidden="true"><path d="M1 3h10v7H1z M1 3l5 4 5-4" fill="var(--brand-blue)" stroke="var(--card)" stroke-width="0.8"/></svg>
      doug@boldpromoperksgroup.example
    </li>
    <li>
      <svg viewBox="0 0 12 12" aria-hidden="true"><circle cx="6" cy="6" r="5"/><path d="M1 6h10M6 1v10" stroke="var(--card)" stroke-width="0.8"/></svg>
      www.BoldPromoPerksGroup.example
    </li>
  </ul>
  <div class="cta-button">
    <svg viewBox="0 0 300 27" width="300" height="27" aria-hidden="true">
      <polygon points="2,6 296,0 300,27 0,27" fill="var(--brand-green)"/>
    </svg>
    <span>GET A FREE SAMPLE PACKAGE</span>
  </div>
</section>

</body>
</html>
```